Very high end short term vacation rentals.

Coral Haven Coast Properties. Design business cards using existing logo. Should represent high quality, class accommodations. The back side will have a QR code linking to website/video and pictures

```html
<!DOCTYPE html>
<html lang="en">
<head>
<meta charset="utf-8">
<title>Coral Haven Coast Properties – Business Cards</title>
<link rel="stylesheet" href="https://fonts.googleapis.com/css2?family=Cinzel:wght@500&family=Poppins:wght@400&display=swap">
<style>
  :root {
    --backdrop: #e6e6e6;
    --card-front: #ffffff;
    --card-back: #050505;
    --ink: #161616;
    --ink-soft: #4a4a4a;
    --paper-text: #f2f2f2;
    --faint-art-a: rgba(210, 210, 210, 0.45);
    --faint-art-b: rgba(255, 255, 255, 0);
  }
  * { margin: 0; padding: 0; box-sizing: border-box; }
  html, body {
    width: 1200px;
    height: 1085px;
    overflow: hidden;
    background: var(--backdrop);
  }
  .card {
    position: absolute;
    left: 300px;
    width: 579px;
    height: 343px;
  }
  .card--front { top: 163px; background: var(--card-front); }
  .card--back { top: 542px; background: var(--card-back); }

  .brand {
    position: absolute;
    display: flex;
    align-items: center;
    gap: 22px;
  }
  .brand__ring {
    width: 96px;
    height: 96px;
    border-radius: 50%;
    border: 2px solid var(--ink);
    flex: none;
  }
  .brand__name {
    font-family: "Cinzel", serif;
    font-weight: 500;
    color: var(--ink);
    line-height: 1.08;
  }
  .brand__line1 { display: block; font-size: 31px; letter-spacing: 0.5px; }
  .brand__line2 { display: block; font-size: 22px; letter-spacing: 1px; }

  .card--front .brand { left: 42px; top: 37px; }

  .faint-art {
    position: absolute;
    right: 0;
    top: 40px;
    width: 300px;
    height: 303px;
    background: radial-gradient(ellipse at 65% 45%, var(--faint-art-a), var(--faint-art-b) 70%);
  }

  .person {
    position: absolute;
    left: 38px;
    top: 180px;
  }
  .person__name {
    font-family: "Cinzel", serif;
    font-weight: 500;
    font-size: 25px;
    color: var(--ink);
    letter-spacing: 0.5px;
  }
  .person__role {
    font-family: "Poppins", sans-serif;
    font-size: 16px;
    color: var(--ink-soft);
    margin-top: -4px;
  }

  .contact {
    position: absolute;
    left: 38px;
    top: 256px;
    list-style: none;
    font-family: "Poppins", sans-serif;
    font-size: 16.5px;
    color: var(--ink);
    line-height: 17.5px;
  }
  .contact li { display: flex; align-items: center; gap: 7px; }
  .contact svg { width: 14px; height: 14px; flex: none; }

  .address {
    position: absolute;
    right: 34px;
    top: 272px;
    text-align: right;
    font-family: "Poppins", sans-serif;
    font-size: 16.5px;
    line-height: 17.5px;
    color: var(--ink);
  }

  .card--back .brand { left: 106px; top: 124px; }
  .card--back .brand__ring { width: 90px; height: 90px; border-color: var(--paper-text); margin-right: 10px; }
  .card--back .brand__name { color: var(--paper-text); }
</style>
</head>
<body>

<section class="card card--front">
  <div class="brand">
    <div class="brand__ring"></div>
    <div class="brand__name">
      <span class="brand__line1">Coral Haven</span>
      <span class="brand__line2">Coast Properties</span>
    </div>
  </div>

  <div class="faint-art" role="img" aria-label="Faint pale grey sketch-style decoration area"></div>

  <div class="person">
    <h1 class="person__name">ELIAS MORROW</h1>
    <p class="person__role">Managing&nbsp; Director</p>
  </div>

  <ul class="contact">
    <li>
      <svg viewBox="0 0 24 24" aria-hidden="true"><path fill="none" stroke="#161616" stroke-width="2.4" stroke-linejoin="round" d="M6 3l3.5 4-2 2.5c1.2 2.8 3.5 5 6 6l2.5-2 4 3.5-2.5 3C10 19.5 4.5 14 3 5.5z"/></svg>
      044-123 456 789
    </li>
    <li>
      <svg viewBox="0 0 24 24" aria-hidden="true"><rect x="2" y="5" width="20" height="14" fill="#161616"/><path d="M2 5l10 8 10-8" fill="none" stroke="#fff" stroke-width="1.6"/></svg>
      info@email.com
    </li>
    <li>
      <svg viewBox="0 0 24 24" aria-hidden="true"><g fill="none" stroke="#161616" stroke-width="1.8"><circle cx="12" cy="12" r="9.5"/><ellipse cx="12" cy="12" rx="4.2" ry="9.5"/><path d="M2.5 12h19M4 7h16M4 17h16"/></g></svg>
      www.website.com
    </li>
  </ul>

  <address class="address" style="font-style:normal">
    123, 7th street<br>
    Country name, 123456
  </address>
</section>

<section class="card card--back">
  <div class="brand">
    <div class="brand__ring"></div>
    <div class="brand__name">
      <span class="brand__line1">Coral Haven</span>
      <span class="brand__line2">Coast Properties</span>
    </div>
  </div>
</section>

</body>
</html>
```